Duct Manufacturing Company new to the industry needs business card and stationary design

we are sheet metal duct manufacturers looking for a business card design to fit my new business logo.
nothing to crazy that will date, but want it to stand out from the crowed.
I'm sure you guys will work it out.

Contact Information for Business Card

Glen Marsh
Director

Address
17 Dorwell St
Bellmount NSW 2631

0438 760 514

Sales@flowbend.com.au

Font styles to use
Other font styles liked:
• BankGothic md bt

Requirements
Nice to have
• Like the idea of corner rounded to match logo
• like to keep colours flowing
• font I like sharp square not rounded

```html
<!DOCTYPE html>
<html lang="en">
<head>
<meta charset="utf-8">
<title>Flowbend Industries – Business Card</title>
<link rel="stylesheet" href="https://fonts.googleapis.com/css2?family=Saira:wght@400;500;600&display=swap">
<style>
  :root {
    --page-bg: #3a3a3a;
    --card-black: #0d0d0e;
    --card-mid: #232325;
    --stripe-green: #5fb52c;
    --stripe-blue: #1273c6;
    --stripe-grey: #9a9a9a;
    --name-blue: #1e96e0;
    --title-green: #63b82e;
    --body-grey: #b9b9b9;
    --divider: #4a4a4d;
  }
  * { margin: 0; padding: 0; box-sizing: border-box; }
  html, body {
    width: 1200px; height: 750px; overflow: hidden;
    background: var(--page-bg);
    font-family: "Saira", sans-serif;
  }
  .card {
    position: absolute; left: 110px; top: 95px;
    width: 980px; height: 560px;
    background:
      repeating-linear-gradient(90deg, rgba(255,255,255,0.015) 0 2px, rgba(0,0,0,0.02) 2px 5px),
      linear-gradient(180deg, rgba(0,0,0,0.6) 0%, rgba(0,0,0,0) 30%, rgba(0,0,0,0) 70%, rgba(0,0,0,0.5) 100%),
      linear-gradient(90deg, var(--card-black) 0%, var(--card-mid) 45%, var(--card-black) 100%);
    display: flex;
  }
  .edge-stripe { width: 22px; display: flex; flex-direction: column; }
  .edge-stripe .seg-green { flex: 1; background: var(--stripe-green); }
  .edge-stripe .seg-blue { flex: 1.02; background: var(--stripe-blue); }
  .edge-stripe .seg-grey { flex: 1; background: var(--stripe-grey); }
  .brand {
    position: absolute; left: 130px; top: 240px; width: 340px;
    display: flex; align-items: center; gap: 14px;
  }
  .brand-mark { width: 22px; height: 22px; background: var(--title-green); flex: none; }
  .brand-name {
    color: var(--title-green); font-weight: 600; font-size: 36px;
    letter-spacing: 1px; line-height: 1.05; text-transform: uppercase;
  }
  .divider {
    position: absolute; left: 510px; top: 150px;
    width: 2px; height: 280px; background: var(--divider);
  }
  .contact { position: absolute; left: 565px; top: 155px; color: var(--body-grey); }
  .contact-name { color: var(--name-blue); font-size: 34px; font-weight: 600; line-height: 1.1; }
  .contact-title { color: var(--title-green); font-size: 24px; font-weight: 400; line-height: 1.2; }
  .contact-address { margin-top: 18px; font-size: 22px; line-height: 1.35; }
  .contact-lines { list-style: none; margin-top: 12px; }
  .contact-lines li {
    display: flex; align-items: center; gap: 14px;
    font-size: 22px; line-height: 38px;
  }
  .contact-lines svg { width: 24px; height: 24px; flex: none; }
</style>
</head>
<body>
  <div class="card">
    <div class="edge-stripe">
      <div class="seg-green"></div>
      <div class="seg-blue"></div>
      <div class="seg-grey"></div>
    </div>

    <div class="brand">
      <span class="brand-mark"></span>
      <span class="brand-name">Flowbend<br>Industries</span>
    </div>

    <div class="divider"></div>

    <div class="contact">
      <div class="contact-name">Glen Marsh</div>
      <div class="contact-title">Director</div>
      <div class="contact-address">17 Dorwell St<br>Bellmount NSW 2631</div>
      <ul class="contact-lines">
        <li>
          <svg viewBox="0 0 24 24" aria-hidden="true"><path fill="#1e96e0" d="M6.6 10.8a15.1 15.1 0 0 0 6.6 6.6l2.2-2.2c.3-.3.7-.4 1-.2 1.1.4 2.3.6 3.6.6.6 0 1 .4 1 1V20c0 .6-.4 1-1 1A17 17 0 0 1 3 4c0-.6.4-1 1-1h3.5c.6 0 1 .4 1 1 0 1.3.2 2.5.6 3.6.1.3 0 .7-.2 1z"/></svg>
          0438 760 514
        </li>
        <li>
          <svg viewBox="0 0 24 24" aria-hidden="true"><rect x="2" y="5" width="20" height="14" fill="#1e96e0"/><path d="M2 5l10 8 10-8" fill="none" stroke="#0d0d0e" stroke-width="1.6"/></svg>
          Sales@flowbend.com.au
        </li>
        <li>
          <svg viewBox="0 0 24 24" aria-hidden="true"><circle cx="12" cy="12" r="10" fill="#1e96e0"/><path d="M2 12h20M12 2c3 3 3 17 0 20M12 2c-3 3-3 17 0 20" fill="none" stroke="#0d0d0e" stroke-width="1.3"/></svg>
          www.flowbend.com.au
        </li>
      </ul>
    </div>
  </div>
</body>
</html>
```